Business cards for Harbourline Supply Pty Ltd that import building products into Australia from China
Target Market(s)
Business to Business
Industry/Entity Type
Business
Contact Information for Business Card
Front: Logo and Business Name
Rear:
Desmond Varrick
General Manager
Mobile: 0427 561 394
email: dessie@harbourlinesupply.com.au
alternative email: dessie@outbackworks.com.au
web: www.harbourlinesupply.com.au
Kelmore, Ashvale and Rivenport
Colors
ec1f27
fbee3d

```html
<!DOCTYPE html>
<html lang="en">
<head>
<meta charset="utf-8">
<title>Harbourline Supply Pty Ltd – Business Cards</title>
<link rel="stylesheet" href="https://fonts.googleapis.com/css2?family=Open+Sans:wght@400;600;700;800&display=swap">
<style>
  :root {
    --brand-red: #ec1f27;
    --brand-yellow: #fbee3d;
    --ink: #1d1d1f;
    --ink-soft: #3a3a3c;
    --paper: #ffffff;
    --card-black: #1b1b1d;
    --backdrop: #2b2b2d;
    --divider: #f3b7b9;
  }
  * { box-sizing: border-box; margin: 0; padding: 0; }
  html, body {
    width: 1200px; height: 900px; overflow: hidden;
    background: var(--backdrop);
    font-family: "Open Sans", Arial, sans-serif;
  }
  .stage {
    position: relative; width: 1200px; height: 900px;
    display: flex; align-items: center; justify-content: center; gap: 50px;
  }
  .card {
    width: 520px; height: 300px; border-radius: 26px;
    position: relative; overflow: hidden;
  }
  .card--back {
    background: var(--paper);
    display: flex; align-items: center;
    padding: 0 30px 0 34px;
  }
  .card--front {
    background: var(--card-black);
    display: flex; align-items: center; justify-content: center;
  }
  .wordmark {
    display: flex; align-items: center; gap: 10px;
    font-weight: 800; line-height: 1.05;
  }
  .wordmark__square {
    width: 26px; height: 26px; background: var(--brand-red); flex: none;
  }
  .wordmark__name { font-size: 22px; color: var(--ink); }
  .card--front .wordmark__name { color: var(--paper); font-size: 28px; }
  .card--front .wordmark__square { width: 32px; height: 32px; }
  .card__brand { width: 205px; flex: none; }
  .card__divider {
    width: 1px; height: 200px; background: var(--divider); margin: 0 18px 0 12px; flex: none;
  }
  .contact { color: var(--ink-soft); }
  .contact__name { font-size: 21px; font-weight: 800; letter-spacing: .5px; color: var(--ink); text-transform: uppercase; }
  .contact__first { color: var(--brand-red); }
  .contact__title { font-size: 12px; font-weight: 600; color: var(--ink); margin: 2px 0 12px; }
  .contact__list { list-style: none; }
  .contact__item {
    display: flex; align-items: center; gap: 8px;
    font-size: 12px; line-height: 1.9;
  }
  .contact__icon { width: 11px; height: 11px; flex: none; fill: var(--brand-red); }
  .contact__region { font-size: 12px; margin-top: 10px; }
</style>
</head>
<body>
<main class="stage">
  <section class="card card--back" aria-label="Card reverse with contact details">
    <div class="card__brand">
      <div class="wordmark">
        <span class="wordmark__square" aria-hidden="true"></span>
        <span class="wordmark__name">Harbourline<br>Supply Pty Ltd</span>
      </div>
    </div>
    <div class="card__divider" aria-hidden="true"></div>
    <div class="contact">
      <h1 class="contact__name"><span class="contact__first">Desmond</span> Varrick</h1>
      <p class="contact__title">General Manager</p>
      <ul class="contact__list">
        <li class="contact__item">
          <svg class="contact__icon" viewBox="0 0 12 12" aria-hidden="true"><path d="M1 3c0-1 1-2 2-2l1.5 2.5L3.3 4.6c.6 1.6 2.4 3.4 4 4l1.1-1.2L11 9c0 1-1 2-2 2C4.6 11 1 7.4 1 3z"/></svg>
          0427 561 394
        </li>
        <li class="contact__item">
          <svg class="contact__icon" viewBox="0 0 12 12" aria-hidden="true"><path d="M0 2h12v8H0z"/><path d="M0 2l6 4.5L12 2" fill="none" stroke="#fff" stroke-width="1"/></svg>
          dessie@harbourlinesupply.com.au
        </li>
        <li class="contact__item">
          <svg class="contact__icon" viewBox="0 0 12 12" aria-hidden="true"><path d="M0 2h12v8H0z"/><path d="M0 2l6 4.5L12 2" fill="none" stroke="#fff" stroke-width="1"/></svg>
          dessie@outbackworks.com.au
        </li>
        <li class="contact__item">
          <svg class="contact__icon" viewBox="0 0 12 12" aria-hidden="true"><circle cx="6" cy="6" r="5.5"/><path d="M.5 6h11M6 .5c-2.5 3-2.5 8 0 11M6 .5c2.5 3 2.5 8 0 11" fill="none" stroke="#fff" stroke-width=".8"/></svg>
          www.harbourlinesupply.com.au
        </li>
      </ul>
      <p class="contact__region">Kelmore, Ashvale and Rivenport</p>
    </div>
  </section>

  <section class="card card--front" aria-label="Card front with business name">
    <div class="wordmark">
      <span class="wordmark__square" aria-hidden="true"></span>
      <span class="wordmark__name">Harbourline<br>Supply Pty Ltd</span>
    </div>
  </section>
</main>
</body>
</html>
```